Shopping center investment profile

We need to design a two-page 8.5" x 11" brochure that can be used as a template for profiling our shopping centers and demonstrating our track record to investors.

Our company (QLM Real Estate Investments) owns retail shopping centers in the southwestern United States. Our website is www.qlmvx.example, but we will be redesigning and modernizing the website and logo in the near future, so please do not use the color schemes or framework of the website for the brochure.

Our investors are institutional and high net worth investors who typically have an existing relationship with our company. They are determining whether to invest multi-millions of dollars in a shopping center opportunity, so the brochure needs to be professional, very high quality and provide key information about the specific property.
Updates

Additional guidance on color scheme:

We would like to see a Blue (something like Hex #5A61BC) and Gold (Hex #EDB215) or (Hex #DDA24B) color scheme with some Black accents 

Thank you!

Target Market(s)

Our target audiences are institutional investors, high net-worth individuals, financial firms and medium to large commercial real estate companies.

Industry/Entity Type

Investment

Requirements
Must have
• Clean and modern look with corresponding fonts and colors.
• Incorporates the information found in the attached "Harborline Commons profile" Pages or PDF file.
• Final file design files that can be modified easily
Nice to have
• Two examples of industry brochures are attached. These are examples of the professional quality that we are looking for, not necessarily the design or format.

```html
<!DOCTYPE html>
<html lang="en">
<head>
<meta charset="utf-8">
<title>Harborline Commons – Property Profile</title>
<link href="https://fonts.googleapis.com/css2?family=Roboto+Condensed:wght@700&family=Arimo:wght@400;700&display=swap" rel="stylesheet">
<style>
  :root{
    --blue:#5a5fb6;
    --gold:#edb215;
    --lavender:#d8d8ee;
    --ink:#1b1b1b;
    --paper:#ffffff;
    --map:#e6e6e6;
    --site:#8e8e8e;
    --rule:#333;
  }
  *{margin:0;padding:0;box-sizing:border-box}
  html,body{width:1200px;height:768px;overflow:hidden;background:var(--paper)}
  body{position:relative;font-family:"Arimo",Arial,sans-serif;color:var(--ink)}
  .page{position:absolute;top:0;width:740px;height:958px;transform:scale(.8);transform-origin:0 0;background:var(--paper);overflow:hidden}
  .page--front{left:0}
  .page--back{left:608px}
  .shapes{position:absolute;inset:0}
  .abs{position:absolute}
  .brand-box{left:38px;top:0;width:127px;height:130px;background:var(--gold);padding:24px 0 0 11px;color:var(--ink)}
  .brand-name{font-size:50px;line-height:46px;letter-spacing:1px}
  .brand-sub{font-size:15.5px;line-height:16px;margin-top:6px}
  .header{left:170px;top:0;width:570px;height:130px;background:var(--blue)}
  .title{left:203px;top:30px;font-family:"Roboto Condensed",sans-serif;font-weight:700;color:#fff;font-size:41px;line-height:48px}
  .subtitle{left:203px;top:76px;font-family:"Roboto Condensed",sans-serif;font-weight:700;color:#fff;font-size:20px}
  .tag{right:24px;top:25px;text-align:right;font-family:"Roboto Condensed",sans-serif;font-weight:700;font-size:16.5px;line-height:20px;color:var(--ink)}
  .photo{background:linear-gradient(180deg,#2f6fcf 0%,#7eaee6 38%,#b06a46 52%,#8a4f35 70%,#3a3a40 78%,#2e2e33 100%)}
  .photo--old{background:linear-gradient(180deg,#a9c6e6 0%,#e4ebf2 42%,#b89d7c 58%,#8f7b66 72%,#a3a3a3 80%,#9a9a9a 100%)}
  .caption{font-family:"Roboto Condensed",sans-serif;font-weight:700;color:#fff;font-size:17px}
  .panel{background:var(--lavender)}
  .h2{font-family:"Roboto Condensed",sans-serif;font-weight:700;font-size:19px;color:var(--ink)}
  .facts{font-size:11px;width:222px;border-collapse:collapse}
  .facts td{padding:3px 5px;border-top:1px solid var(--rule);vertical-align:top}
  .facts tr:last-child td{border-bottom:1px solid var(--rule)}
  .facts td:last-child{text-align:right;white-space:nowrap}
  .bullets{list-style:none;font-size:10.5px;line-height:13px}
  .bullets li{position:relative;padding-left:14px}
  .bullets li::before{content:"";position:absolute;left:1px;top:4px;width:5px;height:5px;border-radius:50%;background:var(--ink)}
  .foot-brand{left:25px;color:#fff}
  .foot-brand .brand-name{font-size:48px;line-height:46px}
  .foot-brand .brand-sub{font-size:15.5px;line-height:16px;margin-top:4px}
  .address{left:25px;top:873px;color:#fff;font-size:10px;line-height:12px}
  .invest{font-size:11px;width:244px;border-collapse:collapse}
  .invest td{padding:3px 2px;border-bottom:1px solid var(--rule)}
  .invest td:last-child{text-align:right}
  .invest .gap td{border:none;height:16px}
  .invest .plain td:first-child{border-bottom:none}
  .challenges .bullets li{margin-bottom:13px}
  .map-title{left:190px;top:666px;font-family:"Roboto Condensed",sans-serif;font-weight:700;color:#fff;font-size:19px}
  .road{font-family:"Arimo",Arial,sans-serif;font-weight:700;font-size:9px;color:var(--ink);letter-spacing:.3px}
  .road--v{transform:rotate(90deg);transform-origin:0 0}
</style>
</head>
<body>

<section class="page page--front">
  <svg class="shapes" viewBox="0 0 740 958" aria-hidden="true">
    <polygon points="0,35 38,60 38,385 165,488 165,958 0,958" fill="var(--blue)"/>
  </svg>
  <div class="abs brand-box"><div class="brand-name">QLM</div><div class="brand-sub">REAL ESTATE<br>INVESTMENTS</div></div>
  <div class="abs header"></div>
  <svg class="shapes" viewBox="0 0 740 958" aria-hidden="true">
    <polygon points="578,0 740,0 740,128" fill="var(--gold)"/>
  </svg>
  <div class="abs title">Harborline Commons</div>
  <div class="abs subtitle">Marlow Springs, Arizona</div>
  <div class="abs tag">Property<br>Profile</div>

  <svg class="abs" style="left:38px;top:135px" width="127" height="350" viewBox="0 0 127 350" role="img" aria-label="Street map locating the property">
    <polygon points="0,0 127,0 127,350 100,350 0,250" fill="var(--map)"/>
    <path d="M48,80 C40,70 38,66 38,62 a10,10 0 0 1 20,0 c0,4 -2,8 -10,18z" fill="var(--gold)"/>
    <circle cx="48" cy="62" r="3.5" fill="#fff"/>
  </svg>

  <div class="abs photo" style="left:170px;top:135px;width:568px;height:353px" role="img" aria-label="Rendering of the renovated shopping center storefronts and parking lot"></div>

  <svg class="shapes" viewBox="0 0 740 958" aria-hidden="true">
    <polygon points="185,490 738,490 738,518 170,518" fill="var(--ink)"/>
  </svg>
  <div class="abs caption" style="left:208px;top:494px">Harborline Commons, Marlow Springs, Arizona</div>
  <div class="abs caption" style="right:38px;top:494px">79.490 sq ft</div>

  <div class="abs panel" style="left:170px;top:520px;width:568px;height:438px"></div>

  <div class="abs h2" style="left:192px;top:558px">Summa</div>
  <table class="abs facts" style="left:187px;top:595px">
    <tr><td>Property Type</td><td>Shopping Center</td></tr>
    <tr><td>Size</td><td>79,490 sq ft</td></tr>
    <tr><td>79,490 sq ft</td><td>April 2011</td></tr>
    <tr><td>Total Investment</td><td>$X,XXX,XXX</td></tr>
    <tr><td>Purchase Occupancy</td><td>8,39%</td></tr>
    <tr><td>Current Occupancy</td><td>97,29%</td></tr>
    <tr><td>Projected 5-year IRR<br>(Unleveraged)</td><td>XX.XX%</td></tr>
  </table>

  <div class="abs h2" style="left:431px;top:561px">Opportunity</div>
  <ul class="abs bullets" style="left:431px;top:599px;width:290px">
    <li>Bank owned property with attractive purchase price</li>
    <li>Strong relationship with seller’s broker<br>and decision makers</li>
    <li>Redevelopment upside with management and leasing</li>
    <li>No major renovations required</li>
    <li>Marlow Springs location has very strong population, education and income demographics</li>
    <li>Adjacent to premier 2,500-residence master planned community of Willow Bend Lakes</li>
    <li>Strong employment area with the new Northgate Regional hospital and the adjacent Coastline Cancer center</li>
  </ul>

  <div class="abs h2" style="left:431px;top:757px">Results</div>
  <ul class="abs bullets" style="left:431px;top:791px;width:280px">
    <li>Stabilized the shopping center within three years, producing excellent results for investors</li>
    <li>Transformed the center into a vibrant destination that the surrounding community is excited about</li>
    <li>Transitioned legacy tenants to upgrade the business operators</li>
    <li>Reduced the shopping center’s operating expenses by replacing vendors and appealing property taxes</li>
  </ul>

  <div class="abs foot-brand" style="top:776px"><div class="brand-name">QLM</div><div class="brand-sub">REAL ESTATE<br>INVESTMENTS</div></div>
  <div class="abs address">2450 W Cedar Lane Suite 300<br>Tempe Vista, AZ 85000<br>(555) 014-2900</div>
</section>

<section class="page page--back">
  <svg class="shapes" viewBox="0 0 740 958" aria-hidden="true">
    <polygon points="0,35 38,60 38,290 165,290 165,958 0,958" fill="var(--blue)"/>
  </svg>
  <div class="abs brand-box"><div class="brand-name">QLM</div><div class="brand-sub">REAL ESTATE<br>INVESTMENTS</div></div>
  <div class="abs header"></div>
  <svg class="shapes" viewBox="0 0 740 958" aria-hidden="true">
    <polygon points="578,0 740,0 740,128" fill="var(--gold)"/>
  </svg>
  <div class="abs title">Harborline Commons</div>
  <div class="abs subtitle">Marlow Springs, Arizona</div>
  <div class="abs tag">Property<br>Profile</div>

  <div class="abs photo photo--old" style="left:38px;top:135px;width:342px;height:153px" role="img" aria-label="Shopping center before renovation"></div>
  <div class="abs photo" style="left:385px;top:135px;width:353px;height:153px" role="img" aria-label="Shopping center after renovation"></div>

  <svg class="shapes" viewBox="0 0 740 958" aria-hidden="true">
    <polygon points="170,290 738,290 738,318 200,318" fill="var(--ink)"/>
  </svg>
  <div class="abs caption" style="left:325px;top:293px">before</div>
  <div class="abs caption" style="right:14px;top:293px">after</div>

  <div class="abs panel" style="left:170px;top:320px;width:568px;height:325px"></div>

  <div class="abs h2" style="left:182px;top:347px">Investment</div>
  <table class="abs invest" style="left:182px;top:385px">
    <tr><td>Purchase Price</td><td>$X,XXX,XXX</td></tr>
    <tr><td>Sponsor Acquisition Fee</td><td>$XX,XXX</td></tr>
    <tr><td>Painting and Landscape</td><td>$XXX,XXX</td></tr>
    <tr><td>TI/LC Reserve</td><td>$X,XXX,XXX</td></tr>
    <tr><td>Operating Expenses</td><td>$XXX,XXX</td></tr>
    <tr><td>Total Cash Investment</td><td></td></tr>
    <tr class="gap"><td></td><td></td></tr>
    <tr><td>Investor / Sponsor Split</td><td>XX% / XX%</td></tr>
    <tr class="plain"><td>Structure</td><td>Cash Flow Pari Passu</td></tr>
    <tr class="plain"><td></td><td>Acquisition Fee</td></tr>
    <tr class="plain"><td></td><td>Management Fee</td></tr>
  </table>

  <div class="abs h2" style="left:436px;top:347px">Challenges and Solutions</div>
  <div class="abs challenges" style="left:436px;top:385px;width:282px">
    <ul class="bullets">
      <li>Nationwide vacancy rate - QLM did significant due diligence on the property before purchasing the asset, and determined that the location is an A/A-; Tenant improvement and leasing commissions were reserved in order to attract national and regional tenants</li>
      <li>Size of Anchor space - QLM determined that a family-friendly entertainment venue would best serve the demographics in the area instead of another grocer; QLM sought out an experienced operator in Funhouse Games, who has multiple locations in three states</li>
      <li>Curb Appeal - With vacancy and a stigma attached to the center, QLM had to change the center’s appeal to the community. QLM worked hand in hand with the Town of Marlow Springs and the Willow Bend Lakes community association to paint the center, upgrade landscaping and add new and larger monument signs</li>
    </ul>
  </div>

  <svg class="abs" style="left:170px;top:648px" width="570" height="310" viewBox="0 0 570 310" role="img" aria-label="Site plan of the center showing pads, parking, landscaping and the anchor tenant">
    <defs>
      <linearGradient id="siteTone" x1="0" y1="0" x2="1" y2="1">
        <stop offset="0" stop-color="#8e8e8e"/>
        <stop offset=".55" stop-color="#9a9f94"/>
        <stop offset="1" stop-color="#8a8a8a"/>
      </linearGradient>
    </defs>
    <polygon points="0,0 510,0 570,48 570,310 0,310" fill="url(#siteTone)"/>
    <g transform="translate(480,218)" fill="#fff">
      <polygon points="0,-26 4,-4 0,0 -4,-4"/>
      <polygon points="0,26 4,4 0,0 -4,4"/>
      <polygon points="-26,0 -4,-4 0,0 -4,4"/>
      <polygon points="26,0 4,-4 0,0 4,4"/>
    </g>
    <text x="480" y="188" font-size="8" text-anchor="middle" fill="#fff" font-family="Arimo,Arial,sans-serif">N</text>
    <text x="480" y="256" font-size="8" text-anchor="middle" fill="#fff" font-family="Arimo,Arial,sans-serif">S</text>
  </svg>
  <div class="abs map-title">Harborline Commons -&nbsp; 97% Occupancy</div>
  <div class="abs road" style="left:505px;top:677px">CEDAR RIDGE ROAD</div>
  <div class="abs road road--v" style="left:618px;top:698px">HARBORLINE ROAD</div>

  <div class="abs foot-brand" style="top:776px"><div class="brand-name">QLM</div><div class="brand-sub">REAL ESTATE<br>INVESTMENTS</div></div>
  <div class="abs address">2450 W Cedar Lane Suite 300<br>Tempe Vista, AZ 85000<br>(555) 014-2900</div>
</section>

</body>
</html>
```